Venture Capital firm needs modern business cards

We are a Venture Capital firm within financial services/Asset management. The industry generally has basic business cards with black, blue and maybe green/yellow design elements.
Our firm has a four-colour swoosh logo. We are based in London and want to stand out, just a little bit!, from the crowd. Our company is called LORV Investments and the 'C' stands for collaboration thus using makerswarm is a natural portal for our business card design competition. Our logo came via makerswarm too!
We use 'Venture Partner in Asset Management' as our tagline and this is Trademark registered. We operate in a conservative industry and we should not overstep our mark. The logo is colorful as it is and therefore the rest of the design should not be too fanciful.
The objective is twofold: make our logo element stick and memorable with our audience, whilst representing a conservative yet young image.
Updates
The Business Card obviously needs a field for Name, Surname, Job Title, Adress fields: Street, City, Postcode, Country, telefone and cell number, website address, etc.
We have uploaded the ai file. We trust that these are OK. If not, please advise.
Reason: We have have been busy with a client engagement. We will set the project as Guaranteed in return for the troubles we cause. Apologies for the confusion.
Thank you all for these great and creative design suggestions. The team is very happy with a number of your ideas! We will be in touch tomorrow to give individual feedback before the project closes on Friday. We look forward to working with some of you to narrow down your creations. Thank you, LORV Investments team.
All,
Target Market(s)
Financial Services Professionals, Investors, Media, 35-70 years, mainly male, well educated
Industry/Entity Type
Conservative
Requirements
Must have
- We must make use of our logo and potential tagline 'Venture Partner in Asset Management' as we are establishing a new Brand and new company in the market.
We can use 'LORV', 'LORV Investments', and 'LORV Investments'+tagline 'Venture Partner in Asset Management' or simply the four-colour swoosh plus the name of the company as part of the text. (see files)
All design elements are available in black or grey-scale if required. (grey scale swoosh attached).
Due to regulation we must have the following wording on the card in small print 'LORV Investments is an Appointed Representative of Bramwell Holdings Partnership Limited, which is authorised by the Monetary Oversight Board'.
Nice to have
- We would consider designs that make use of different printing techniques such embossing/debossing, UV spot etc.
We attach our colour palette in the files section for your reference.
Should not have
- The font we use for our company name is 'EXO' so do not use a font style that clashes with the corporate fonts, please.
Do not use other design elements than the ones we provide in the file library as part of this project.

```html
<!DOCTYPE html>
<html lang="en">
<head>
<meta charset="utf-8">
<title>LORV Investments – Business Card</title>
<link rel="stylesheet" href="https://fonts.googleapis.com/css2?family=Roboto+Condensed:wght@700&family=Roboto:wght@300;400;500&display=swap">
<style>
  :root {
    --backdrop: #e9e9e9;
    --card: #fbfbfa;
    --card-edge: #dcdcda;
    --ink: #55585b;
    --ink-soft: #8a8d90;
    --ink-fine: #a3a5a7;
    --accent-green: #7cc242;
  }
  * { box-sizing: border-box; margin: 0; padding: 0; }
  html, body {
    width: 1200px;
    height: 800px;
    overflow: hidden;
    background: var(--backdrop);
    font-family: "Roboto", "Helvetica Neue", Arial, sans-serif;
    color: var(--ink);
  }
  .stage {
    width: 1200px;
    height: 800px;
    display: flex;
    align-items: center;
    justify-content: center;
    gap: 80px;
  }
  .card {
    position: relative;
    width: 330px;
    height: 512px;
    background: var(--card);
    border: 1px solid var(--card-edge);
    box-shadow: 0 6px 18px rgba(0,0,0,0.08);
  }

  /* Brand name set in the card's text face */
  .brand {
    display: flex;
    align-items: center;
    gap: 10px;
  }
  .brand-dot {
    width: 22px;
    height: 22px;
    border-radius: 50%;
    background: var(--ink);
  }
  .brand-name {
    font-family: "Roboto", "Helvetica Neue", Arial, sans-serif;
    font-weight: 500;
    color: var(--ink);
    letter-spacing: 0.5px;
  }

  /* Back side */
  .card-back .brand {
    position: absolute;
    top: 190px;
    left: 0;
    right: 0;
    justify-content: center;
  }
  .card-back .brand-name { font-size: 56px; line-height: 1; }
  .card-back .tagline {
    position: absolute;
    top: 262px;
    left: 0;
    right: 0;
    text-align: center;
    font-size: 10px;
    color: var(--ink-soft);
    letter-spacing: 0.3px;
  }

  /* Front side */
  .card-front .content {
    position: absolute;
    top: 58px;
    left: 46px;
    right: 36px;
  }
  .card-front .brand-name { font-size: 46px; line-height: 1; }
  .holder-name {
    margin-top: 18px;
    font-family: "Roboto Condensed", "Arial Narrow", sans-serif;
    font-weight: 700;
    font-size: 21px;
    color: var(--accent-green);
    text-transform: uppercase;
    letter-spacing: 0.2px;
  }
  .holder-role {
    margin-top: 2px;
    font-weight: 300;
    font-size: 14px;
    color: var(--ink-soft);
  }
  .contact-list {
    list-style: none;
    margin-top: 26px;
  }
  .contact-item {
    display: flex;
    align-items: flex-start;
    gap: 14px;
    font-weight: 300;
    font-size: 13.5px;
    line-height: 1.35;
    color: var(--ink-soft);
    margin-bottom: 10px;
  }
  .contact-icon {
    flex: 0 0 14px;
    width: 14px;
    height: 16px;
    margin-top: 1px;
  }
  .legal-note {
    position: absolute;
    left: 46px;
    right: 44px;
    bottom: 48px;
    font-size: 6.5px;
    line-height: 1.45;
    color: var(--ink-fine);
  }
</style>
</head>
<body>
<main class="stage">

  <section class="card card-back" aria-label="Business card, back">
    <div class="brand">
      <span class="brand-dot"></span>
      <span class="brand-name">lorv</span>
    </div>
    <p class="tagline">Venture Partner in Asset Management</p>
  </section>

  <section class="card card-front" aria-label="Business card, front">
    <div class="content">
      <div class="brand">
        <span class="brand-dot"></span>
        <span class="brand-name">lorv</span>
      </div>
      <h1 class="holder-name">Marcus Elwood</h1>
      <p class="holder-role">Graphic designer</p>

      <ul class="contact-list">
        <li class="contact-item">
          <svg class="contact-icon" viewBox="0 0 14 16" aria-hidden="true">
            <rect x="3" y="1" width="8" height="14" rx="1.5" fill="none" stroke="#8a8d90" stroke-width="1.2"/>
            <line x1="6" y1="12.5" x2="8" y2="12.5" stroke="#8a8d90" stroke-width="1.2"/>
          </svg>
          <span>+63 2 9876 543</span>
        </li>
        <li class="contact-item">
          <svg class="contact-icon" viewBox="0 0 14 16" aria-hidden="true">
            <rect x="0.6" y="3.5" width="12.8" height="9" fill="none" stroke="#8a8d90" stroke-width="1.2"/>
            <polyline points="0.8,3.8 7,9 13.2,3.8" fill="none" stroke="#8a8d90" stroke-width="1.2"/>
          </svg>
          <span>http://www.lorv.net</span>
        </li>
        <li class="contact-item">
          <svg class="contact-icon" viewBox="0 0 14 16" aria-hidden="true">
            <path d="M7 15 C3 10 2 8 2 6 A5 5 0 0 1 12 6 C12 8 11 10 7 15 Z" fill="#8a8d90"/>
            <circle cx="7" cy="6" r="1.8" fill="#fbfbfa"/>
          </svg>
          <span>48 Alder st.<br>Marlow Heights<br>Eastgate city<br>2100</span>
        </li>
      </ul>
    </div>

    <p class="legal-note">LORV Investments is an Appointed Representative of Bramwell Holdings Partnership Limited, which is authorised by the Monetary Oversight Board</p>
  </section>

</main>
</body>
</html>
```